Property management company looking for modern card design

We at Blue Heron Partners provides property management services for its residential and commercial properties, with expertise in all categories of multifamily, industrial and office projects throughout California.

We need a business card design that is professional and modern designed business card. In our field, clients get hundreds of business cards, we would like our card to stand out.

Please avoid small print.

Target Market(s)

Professionals and high end clients

Industry/Entity Type

Financial Planning

Contact Information for Business Card

Company Name: Blue Heron Partners, Name, email, license #, phone number, website blueheronpartners.com

Font styles to use
Sans Serif

Requirements
Must have
• The card design needs to be adaptable because there is a possibly we will be expanding into different sectors other than real estate. The card design should be focused on financial planning and asset management.
Nice to have
• Modern and simple business card. Eye catching. Non-standard size/shaped cards would be great.
• blueheronpartners.com
Should not have
• Too many bright color or any pictures or shapes of real estate stuff.

```html
<!DOCTYPE html>
<html lang="en">
<head>
<meta charset="utf-8">
<title>Blue Heron Partners – Business Card</title>
<link rel="stylesheet" href="https://fonts.googleapis.com/css2?family=Open+Sans:wght@400;600&display=swap">
<style>
  :root {
    --backdrop: #3b312d;
    --card: #161616;
    --card-edge: #232323;
    --accent: #d8262f;
    --ink-light: #f2f2f2;
  }
  * { box-sizing: border-box; margin: 0; padding: 0; }
  html, body {
    width: 1200px; height: 716px; overflow: hidden;
    background: var(--backdrop);
    font-family: "Open Sans", Arial, sans-serif;
  }
  .stage {
    position: relative; width: 1200px; height: 716px;
    display: flex; align-items: center; justify-content: center; gap: 44px;
  }
  .card {
    position: relative; width: 530px; height: 303px;
    background: linear-gradient(160deg, var(--card-edge), var(--card) 55%);
    border-radius: 18px;
    box-shadow: 0 10px 28px rgba(0,0,0,.45);
  }
  .brand {
    position: absolute; left: 0; right: 0;
    display: flex; align-items: center; justify-content: center;
  }
  .brand-dot {
    flex: none; border-radius: 50%;
    background: var(--accent);
  }
  .brand-name {
    color: var(--accent); font-weight: 600; text-transform: uppercase;
    white-space: nowrap;
  }

  /* back: contact side */
  .card--contact .brand { top: 62px; gap: 12px; }
  .card--contact .brand-dot { width: 20px; height: 20px; }
  .card--contact .brand-name { font-size: 22px; letter-spacing: 3px; }
  .holder {
    position: absolute; top: 150px; right: 310px; text-align: right;
  }
  .holder-name { color: var(--accent); font-size: 17px; line-height: 26px; }
  .holder-licence { color: var(--ink-light); font-size: 15px; line-height: 26px; margin-top: 26px; }
  .divider {
    position: absolute; left: 234px; top: 148px; width: 2px; height: 82px;
    background: var(--ink-light);
  }
  .contact-list {
    position: absolute; left: 252px; top: 150px; list-style: none;
  }
  .contact-list li {
    display: flex; align-items: center; gap: 10px;
    color: var(--ink-light); font-size: 15px; line-height: 26px;
  }
  .contact-icon { width: 16px; height: 16px; flex: none; }

  /* front: brand side */
  .card--brand .brand { top: 128px; gap: 16px; }
  .card--brand .brand-dot { width: 30px; height: 30px; }
  .card--brand .brand-name { font-size: 30px; letter-spacing: 3px; }
</style>
</head>
<body>
<main class="stage">
  <section class="card card--contact">
    <div class="brand">
      <span class="brand-dot"></span>
      <span class="brand-name">Blue Heron Partners</span>
    </div>
    <div class="holder">
      <p class="holder-name">Marcus Delvane</p>
      <p class="holder-licence">Lic : 20459316</p>
    </div>
    <div class="divider"></div>
    <ul class="contact-list">
      <li>
        <svg class="contact-icon" viewBox="0 0 16 16" aria-hidden="true">
          <rect width="16" height="16" rx="3" fill="#d8262f"/>
          <path d="M5 3.5l2 2-1 1.2a6 6 0 0 0 3.3 3.3l1.2-1 2 2-1.2 1.5C7.5 12.3 3.7 8.5 3.5 4.7z" fill="#fff"/>
        </svg>415-555-0186
      </li>
      <li>
        <svg class="contact-icon" viewBox="0 0 16 16" aria-hidden="true">
          <rect width="16" height="16" rx="3" fill="#d8262f"/>
          <rect x="3" y="4.5" width="10" height="7" fill="none" stroke="#fff" stroke-width="1.2"/>
          <path d="M3 4.5l5 4 5-4" fill="none" stroke="#fff" stroke-width="1.2"/>
        </svg>marcus@blueheronpartners.com
      </li>
      <li>
        <svg class="contact-icon" viewBox="0 0 16 16" aria-hidden="true">
          <rect width="16" height="16" rx="3" fill="#d8262f"/>
          <circle cx="8" cy="8" r="4.6" fill="none" stroke="#fff" stroke-width="1.1"/>
          <path d="M3.4 8h9.2M8 3.4c-2 2.6-2 6.6 0 9.2M8 3.4c2 2.6 2 6.6 0 9.2" fill="none" stroke="#fff" stroke-width="1"/>
        </svg>blueheronpartners.com
      </li>
    </ul>
  </section>

  <section class="card card--brand">
    <div class="brand">
      <span class="brand-dot"></span>
      <span class="brand-name">Blue Heron Partners</span>
    </div>
  </section>
</main>
</body>
</html>
```